Hair and Wellness Brochure and Pricelist design

I am requiring a brochure that has a fresh, though alternative design. My business name is The Quiet Orchard Hair and Wellness. I have a very professional approach to my work and love to give that little bit extra to all of my clients. My passion for health, has led me to channel my business alternatively by using non toxic colours and styling products and through that same vein, I have studied Aromatherapy, Indian Head Massage and Reiki...all additional services I use where required.
My studio has very neutral tones of beige,white and beech wood but these tones aren't necessarily required for the brochure.I like to create a space of calm, peace and quiet, where my clients feel refreshed and rejuvenated..

Industry/Entity Type

Business

```html
<!DOCTYPE html>
<html lang="en">
<head>
<meta charset="utf-8">
<title>Colour Services Price List</title>
<link href="https://fonts.googleapis.com/css2?family=PT+Sans&display=swap" rel="stylesheet">
<style>
  :root {
    --cream: #f3f1de;
    --box-brown: #7c6957;
    --box-text: #ffffff;
    --note-text: #6e5e4e;
    --band-light: #d6cbb8;
    --band-soft: #b9a891;
    --band-mid: #9c8872;
    --band-deep: #7c6855;
  }
  html, body {
    margin: 0;
    padding: 0;
    overflow: hidden;
  }
  body {
    width: 1200px;
    height: 2770px;
    font-family: "PT Sans", sans-serif;
  }
  .pricelist {
    position: relative;
    width: 1200px;
    height: 2770px;
    overflow: hidden;
    background: var(--cream);
  }
  .floral-backdrop {
    position: absolute;
    inset: 0;
    background: var(--cream);
  }
  .service {
    position: absolute;
    left: 281px;
    width: 789px;
    box-sizing: border-box;
    display: flex;
    flex-direction: column;
    justify-content: center;
    align-items: center;
    text-align: center;
    background: var(--box-brown);
    color: var(--box-text);
    border-radius: 16px;
    box-shadow: 0 4px 10px rgba(80, 60, 40, 0.35);
    font-size: 49px;
    line-height: 1.3;
    padding: 0 40px;
  }
  .service p { margin: 0; }
  .service--regrowth { top: 165px; height: 277px; }
  .service--half-head { top: 562px; height: 241px; }
  .service--full-head { top: 946px; height: 241px; }
  .service--additional { top: 1307px; height: 290px; }
  .consult-note {
    position: absolute;
    top: 1780px;
    left: 0;
    width: 1200px;
    margin: 0;
    text-align: center;
    font-size: 36px;
    color: var(--note-text);
  }
  .footer-bands {
    position: absolute;
    left: 0;
    top: 1850px;
    width: 1200px;
    height: 920px;
  }
</style>
</head>
<body>
<main class="pricelist">
  <div class="floral-backdrop" role="img" aria-label="Faint pale lily flower pattern across the cream background"></div>

  <section class="service service--regrowth">
    <p>Tint &amp; semi permanent regrowth colour</p>
    <p>$60</p>
  </section>

  <section class="service service--half-head">
    <p>Half head foiling techniques</p>
    <p>$60</p>
  </section>

  <section class="service service--full-head">
    <p>Full head foiling techniques</p>
    <p>$120</p>
  </section>

  <section class="service service--additional">
    <p>Any additional colour with the above colour services starts from</p>
    <p>$20</p>
  </section>

  <p class="consult-note">* Corrective colour services are priced at consultation</p>

  <svg class="footer-bands" viewBox="0 0 1200 920" aria-hidden="true">
    <path d="M0 470 C400 340 800 170 1200 45 L1200 920 L0 920 Z" fill="var(--band-light)"/>
    <path d="M0 570 C400 450 800 320 1200 250 L1200 920 L0 920 Z" fill="var(--band-soft)"/>
    <path d="M0 700 C400 610 800 540 1200 510 L1200 920 L0 920 Z" fill="var(--band-mid)"/>
    <path d="M0 810 C400 770 800 735 1200 720 L1200 920 L0 920 Z" fill="var(--band-deep)"/>
  </svg>
</main>
</body>
</html>
```